Supplement Brand Product Labels

Product Label for Supplement Brand

Protein Powder Label (2 x different flavours)

Neon Colours / Skull / Spooky
Refer to pictures below, they are the look we are wanting to go with but put our touch to it aswell.

Target Market(s)

Fitness

Industry/Entity Type

Supplement Brand

Colors
0054AA
0677BA
7BADD7
CADEEF
E8F1F8
0094D4
00A9DD
6FCCEA
C7EBF8
E9F6FB
00AB8E
00BBA5
67D7C9
C6EFE9
E9F9F6
59FF00
82FF00
B8FF75
E3FFCB
F4FFEA
FFF300
FFF600
FEFA6F
FFFEC7
FFFEE8
FFC000
F8CF3A
FAE287
FDF2CF
FEFAEE
F0912C
F2A743
F7CA91
FBE8D2
FDF5EE
EE7325
F08F49
F5BC92
FAE3D3
FDF4ED
EB3D1F
EC4F4E
F09395
F8D3D4
FCEDEE
E54698
E96AAD
F1A4CE
F9D9EA
FCEFF6
A7469A
B969AE
D3A5CF
EDDBEB
F8F0F9
6B429C
8869AF
B7A5CE
E3DAEB
F3F0F8

Requirements
Nice to have
• Skull, Neon Colours, Abstract, Barbell, Lighting Bolt, Flames, Spooky

```html
<!DOCTYPE html>
<html lang="en">
<head>
<meta charset="utf-8">
<title>Protein Powder Label – Back Panel</title>
<link href="https://fonts.googleapis.com/css2?family=Nunito+Sans:wght@400;600;700;800&display=swap" rel="stylesheet">
<style>
  :root {
    --ink: #ffffff;
    --ink-soft: #e9e4f0;
    --night: #07060c;
    --violet-deep: #2a1240;
    --violet: #6b429c;
    --magenta: #a7469a;
    --pink-glow: #e54698;
    --teal-dark: #0d2a2c;
    --rule: rgba(255,255,255,0.55);
    --body-font: "Nunito Sans", sans-serif;
  }
  * { margin: 0; padding: 0; box-sizing: border-box; }
  html, body { width: 1016px; height: 1200px; overflow: hidden; background: var(--night); }
  .label {
    position: relative;
    width: 1016px; height: 1200px;
    overflow: hidden;
    font-family: var(--body-font);
    color: var(--ink);
    background:
      radial-gradient(ellipse 360px 300px at 880px 120px, rgba(167,70,154,0.75), transparent 70%),
      radial-gradient(ellipse 420px 380px at 520px 420px, rgba(107,66,156,0.85), transparent 72%),
      radial-gradient(ellipse 380px 260px at 900px 760px, rgba(42,18,64,0.9), transparent 70%),
      radial-gradient(ellipse 520px 300px at 200px 1050px, rgba(13,42,44,0.9), transparent 70%),
      linear-gradient(160deg, #0c0714 0%, #1b0d2b 35%, #231034 60%, #0a0a10 100%);
  }
  .artwork-skull {
    position: absolute;
    left: 234px; top: 0; width: 500px; height: 875px;
    background:
      radial-gradient(ellipse 210px 300px at 250px 440px, rgba(229,70,152,0.35), transparent 70%),
      radial-gradient(ellipse 180px 260px at 250px 420px, rgba(30,12,40,0.9), rgba(20,8,30,0.5) 70%, transparent 100%);
  }
  .nutrition { position: absolute; left: 81px; top: 84px; width: 560px; font-size: 16px; }
  .nutrition-head { position: relative; height: 70px; font-weight: 600; line-height: 1.2; }
  .nutrition-head .serves { position: absolute; left: 0; top: 0; }
  .nutrition-head .col { position: absolute; top: 0; width: 150px; text-align: center; }
  .nutrition-head .col-serve { left: 230px; }
  .nutrition-head .col-100 { left: 421px; }
  .nutrient { position: absolute; left: 0; width: 560px; }
  .nutrient span { position: absolute; top: 0; }
  .nutrient .name { left: 0; }
  .nutrient.sub .name { left: 22px; }
  .nutrient .per-serve { left: 230px; width: 150px; text-align: center; }
  .nutrient .per-100 { left: 421px; width: 150px; text-align: center; }

  .amino { position: absolute; left: 700px; top: 82px; width: 296px; font-size: 16px; }
  .amino h2 { font-size: 20px; font-weight: 800; letter-spacing: 0.2px; margin-bottom: 8px; }
  .amino-row { display: flex; justify-content: space-between; height: 35.6px; align-items: center; padding-left: 6px; }
  .amino-row.head { font-weight: 700; border-bottom: 1.5px solid var(--rule); height: 30px; margin-bottom: 6px; }

  .info { position: absolute; left: 81px; width: 560px; }
  .info h3 { font-size: 21px; font-weight: 800; margin-bottom: 6px; }
  .info p { font-size: 15px; line-height: 1.55; color: var(--ink-soft); }
  .ingredients { top: 528px; }
  .allergens { top: 667px; }
  .directions { top: 752px; }

  .disclaimer { position: absolute; left: 81px; top: 866px; width: 858px; font-size: 14.6px; line-height: 1.6; color: var(--ink-soft); }
  .storage { position: absolute; left: 81px; top: 958px; font-size: 15px; font-weight: 700; }
  .batch-box { position: absolute; left: 700px; top: 970px; width: 233px; height: 142px; border: 2.5px solid var(--ink); }

  .brand { position: absolute; left: 86px; top: 1058px; font-size: 40px; font-weight: 800; color: var(--ink); letter-spacing: 1px; }
  .origin { position: absolute; left: 450px; top: 1094px; display: flex; align-items: center; gap: 10px; }
  .origin .map-mark { width: 44px; height: 38px; background: var(--ink); border-radius: 4px; }
  .origin .text { font-size: 20px; font-weight: 800; line-height: 1.0; }
</style>
</head>
<body>
<main class="label">
  <div class="artwork-skull" role="img" aria-label="Illustration of a dark purple skull hanging from a chain, lit by neon pink light with lightning and smoke"></div>

  <section class="nutrition">
    <div class="nutrition-head">
      <div class="serves">6.25 Servings Per 500g Packet<br>80 Grams Per Serve</div>
      <div class="col col-serve">Average Quantity<br>Per Serving</div>
      <div class="col col-100">Average Quantity<br>Per 100g</div>
    </div>
    <div class="nutrient" style="top:79px"><span class="name">Energy (KJ)</span><span class="per-serve">1286</span><span class="per-100">1608</span></div>
    <div class="nutrient" style="top:136px"><span class="name">Protein (G)</span><span class="per-serve">24.3</span><span class="per-100">30.4</span></div>
    <div class="nutrient" style="top:196px"><span class="name">Fat, Total (G)</span><span class="per-serve">1.7</span><span class="per-100">2.1</span></div>
    <div class="nutrient sub" style="top:227px"><span class="name">Saturated (G)</span><span class="per-serve">1.1</span><span class="per-100">1.3</span></div>
    <div class="nutrient" style="top:282px"><span class="name">Carbohydrates (G)</span><span class="per-serve">47.6</span><span class="per-100">59.5</span></div>
    <div class="nutrient sub" style="top:313px"><span class="name">Sugar (G)</span><span class="per-serve">3.5</span><span class="per-100">4.4</span></div>
    <div class="nutrient" style="top:375px"><span class="name">Sodium (MG)</span><span class="per-serve">68</span><span class="per-100">85</span></div>
  </section>

  <section class="amino">
    <h2>Typical Amino Acid Profile</h2>
    <div class="amino-row head"><span>Amino Acid</span><span>MG/100G</span></div>
    <div class="amino-row"><span>Alanine (mg)</span><span>1619</span></div>
    <div class="amino-row"><span>Arginine (mg)</span><span>920</span></div>
    <div class="amino-row"><span>Aspartic Acid (mg)</span><span>3564</span></div>
    <div class="amino-row"><span>Cystine (mg)</span><span>771</span></div>
    <div class="amino-row"><span>Glutamic Acid (mg)</span><span>5863</span></div>
    <div class="amino-row"><span>Glycine (mg)</span><span>620</span></div>
    <div class="amino-row"><span>Histidine (mg)</span><span>628</span></div>
    <div class="amino-row"><span>Isoleucine (mg)</span><span>1861</span></div>
    <div class="amino-row"><span>Leucine (mg)</span><span>3480</span></div>
    <div class="amino-row"><span>Lysine (mg)</span><span>2913</span></div>
    <div class="amino-row"><span>Methionine (mg)</span><span>792</span></div>
    <div class="amino-row"><span>Phenylalanine (mg)</span><span>1154</span></div>
    <div class="amino-row"><span>Proline (mg)</span><span>2400</span></div>
    <div class="amino-row"><span>Serine (mg)</span><span>1803</span></div>
    <div class="amino-row"><span>Threonine (mg)</span><span>2238</span></div>
    <div class="amino-row"><span>Tryptophan (mg)</span><span>529</span></div>
    <div class="amino-row"><span>Tyrosine (mg)</span><span>1112</span></div>
    <div class="amino-row"><span>Valine (mg)</span><span>1759</span></div>
  </section>

  <section class="info ingredients">
    <h3>Ingredients</h3>
    <p>Maltodextrin, Whey Protein Concentrate, Milk Protein Isolate, Whey Protein Isolate, Branch Chain Amino Acids, Albumin, Wheaten Cornflour, Wholemeal Flour, Cocoa, Flavour, Sucralose.</p>
  </section>
  <section class="info allergens">
    <h3>Allergens</h3>
    <p>Egg, Milk, Soy, Wheat, Gluten.</p>
  </section>
  <section class="info directions">
    <h3>Directions Of Use</h3>
    <p>Mix 2 heaped scoop (40 grams) with 250ml of water or milk and consume immediately. For optimal results, consume 2 – 3 times per day.</p>
  </section>

  <p class="disclaimer">Formulated supplementary sports food. Not suitable for children under 15 years of age or pregnant women. Should only be used under medical or dietetic supervision. This product is not a sole source of nutrition and should be consumed in conjunction with a nutritious diet and appropriate physical training or exercise program.</p>
  <p class="storage">Store in a cool dry place out of direct sunlight.</p>
  <div class="batch-box"></div>

  <div class="brand">VOLTHAUS</div>
  <div class="origin">
    <div class="map-mark" role="img" aria-label="Country outline mark"></div>
    <div class="text">MADE IN<br>AUSTRALIA</div>
  </div>
</main>
</body>
</html>
```